i need a business card for a plumbing company in california

we are a drain cleaning , maintenance plumbing company who is starting new marketing campaign for a tatrench-less pipe installation department .

Target Market(s)

the professional who appreciates time and quality workmanship.

Industry/Entity Type

Plumbing

Colors
0655a3
ec1f27

Requirements
Must have
• the second logo needs to be included
Nice to have
• a focus on the services offered
Should not have
• any underlined words on the brief

```html
<!DOCTYPE html>
<html lang="en">
<head>
<meta charset="utf-8">
<title>Clearline Plumbing – Business Card</title>
<link href="https://fonts.googleapis.com/css2?family=Arimo:wght@400;700&display=swap" rel="stylesheet">
<style>
  :root {
    --backdrop: #232323;
    --card-top: #181818;
    --card-bottom: #0c0c0c;
    --accent-red: #ec1f27;
    --logo-grey: #8e8b85;
    --text-light: #d9d9d9;
    --text-muted: #bdbdbd;
    --divider: #4a4a4a;
  }
  * { margin: 0; padding: 0; box-sizing: border-box; }
  html, body { width: 1200px; height: 900px; overflow: hidden; }
  body {
    background: var(--backdrop);
    font-family: "Arimo", Arial, sans-serif;
    position: relative;
  }
  .card {
    position: absolute;
    left: 320px;
    width: 560px;
    height: 320px;
    background: linear-gradient(160deg, var(--card-top), var(--card-bottom));
    overflow: hidden;
  }
  .card::after {
    content: "";
    position: absolute;
    left: 0; right: 0; bottom: 0;
    height: 11px;
    background: var(--accent-red);
  }
  .card--front { top: 100px; }
  .card--back { top: 470px; }

  /* Front */
  .brand {
    position: absolute;
    top: 108px;
    left: 0; right: 0;
    display: flex;
    justify-content: center;
    align-items: center;
    gap: 14px;
  }
  .brand__name {
    color: var(--logo-grey);
    font-weight: 700;
    font-size: 42px;
    letter-spacing: 0.5px;
  }
  .brand__mark {
    width: 22px; height: 22px;
    background: var(--accent-red);
  }
  .front__web {
    position: absolute;
    top: 218px;
    left: 0; right: 0;
    text-align: center;
    color: var(--accent-red);
    font-size: 15px;
    letter-spacing: 2.5px;
  }

  /* Back */
  .person {
    position: absolute;
    top: 100px;
    right: 312px;
    text-align: right;
  }
  .person__name {
    color: var(--accent-red);
    font-weight: 700;
    font-size: 18px;
    letter-spacing: 0.5px;
  }
  .person__role {
    color: var(--text-muted);
    font-size: 15px;
    margin-top: 4px;
  }
  .divider {
    position: absolute;
    left: 272px;
    top: 78px;
    width: 1px;
    height: 120px;
    background: var(--divider);
  }
  .contacts {
    position: absolute;
    top: 82px;
    left: 292px;
    list-style: none;
  }
  .contacts li {
    display: flex;
    align-items: center;
    gap: 10px;
    color: var(--text-light);
    font-size: 15px;
    height: 27px;
  }
  .contacts svg { width: 14px; height: 14px; fill: var(--accent-red); flex: none; }
  .address {
    position: absolute;
    left: 44px;
    top: 240px;
    color: var(--text-light);
    font-size: 15px;
  }
</style>
</head>
<body>

<section class="card card--front">
  <div class="brand">
    <span class="brand__name">Clearline Plumbing</span>
    <span class="brand__mark"></span>
  </div>
  <p class="front__web">www.clearlineplumb.com</p>
</section>

<section class="card card--back">
  <div class="person">
    <p class="person__name">DANIEL REYES</p>
    <p class="person__role">Managing Director</p>
  </div>
  <div class="divider"></div>
  <ul class="contacts">
    <li>
      <svg viewBox="0 0 16 16"><path d="M2 6c0-2 2-3 6-3s6 1 6 3v1h-3V5.5C10 5 6 5 5 5.5V7H2zM4 8h8l2 5H2z"/></svg>
      044-555 010 234
    </li>
    <li>
      <svg viewBox="0 0 16 16"><path d="M4 1h8v14H4zM5.5 2.5v9h5v-9zM7 12.5h2v1.5H7z" fill-rule="evenodd"/></svg>
      044-555 010 234
    </li>
    <li>
      <svg viewBox="0 0 16 16"><path d="M1 3h14v10H1zM2.5 4.5L8 9l5.5-4.5z" fill-rule="evenodd"/></svg>
      hello@clearlineplumb.com
    </li>
    <li>
      <svg viewBox="0 0 16 16"><circle cx="8" cy="8" r="7"/><path d="M1 8h14M8 1c3 3 3 11 0 14M8 1c-3 3-3 11 0 14" stroke="#0c0c0c" stroke-width="1" fill="none"/></svg>
      www.clearlineplumb.com
    </li>
  </ul>
  <p class="address">480 Harbor Street, Oakridge, California 95001.</p>
</section>

</body>
</html>
```